Harbourline Electrical Solutions

On one side. LOGO (underneath:) Commercial Industrial Residential

- NAME & CONTACT DETAILS

Marcus T. Hollings
Project Manager

(Cell icon) (441) 555-0187
(Email icon) hlelectricalsolutions@mailvento.com
(Facebook & Instagram icons )@hlelectricalsolutions

Other side: LOGO - underneath ELECTRICAL CONSTRUCTION & MAINTENANCE . LED LIGHTING & AUTOMATION . LIFE SAFETY SYSTEMS (FIRE ALARM / SECURITY) . DATA & COMMUNICATION

```html
<!DOCTYPE html>
<html lang="en">
<head>
<meta charset="utf-8">
<title>Harbourline Electrical Solutions – Business Card</title>
<link href="https://fonts.googleapis.com/css2?family=Montserrat:wght@400;500;600;700&family=Lato:wght@400;700&display=swap" rel="stylesheet">
<style>
  :root {
    --teal: #13566a;
    --charcoal: #4b4b4d;
    --paper: #ffffff;
    --ink-grey: #5a5a5c;
    --rule: #c9c9c9;
    --backdrop: #e6e7e8;
  }
  * { box-sizing: border-box; margin: 0; padding: 0; }
  html, body {
    width: 1200px; height: 1015px; overflow: hidden;
    background: var(--backdrop);
  }
  .sheet {
    width: 1200px; height: 1015px;
    display: flex; flex-direction: column; align-items: center; justify-content: center;
    gap: 34px;
  }
  .card {
    width: 800px; height: 457px;
    position: relative; overflow: hidden;
    box-shadow: 0 6px 18px rgba(0,0,0,.18);
  }

  /* Back side */
  .card--back { background: var(--teal); }
  .card--back .upper {
    position: absolute; inset: 0 0 auto 0; height: 245px;
    background: var(--charcoal);
    display: flex; align-items: center; justify-content: center;
  }
  .brand-name--light {
    font-family: "Montserrat", sans-serif; font-weight: 700;
    color: var(--paper); font-size: 38px; letter-spacing: 2px;
    text-transform: uppercase; text-align: center; line-height: 1.2;
  }
  .services {
    position: absolute; left: 0; right: 0; top: 265px;
    list-style: none; text-align: center;
    font-family: "Montserrat", sans-serif; font-weight: 600;
    color: var(--paper); font-size: 19px; line-height: 1.5; letter-spacing: .4px;
    text-transform: uppercase;
  }

  /* Front side */
  .card--front { background: var(--paper); }
  .card--front .band {
    position: absolute; left: 0; right: 0; bottom: 0; height: 92px;
    background: var(--teal);
  }
  .front-content {
    position: absolute; left: 0; right: 0; top: 38px;
    display: flex; flex-direction: column; align-items: center; text-align: center;
  }
  .brand {
    display: flex; align-items: center; gap: 14px;
  }
  .brand-mark { width: 22px; height: 22px; background: var(--teal); }
  .brand-name {
    font-family: "Montserrat", sans-serif; font-weight: 600;
    color: var(--teal); font-size: 28px; letter-spacing: 2px; text-transform: uppercase;
  }
  .sectors {
    margin-top: 10px;
    font-family: "Montserrat", sans-serif; font-weight: 400;
    color: var(--ink-grey); font-size: 17px; letter-spacing: 1.5px; text-transform: uppercase;
  }
  .person-name {
    margin-top: 30px;
    font-family: "Montserrat", sans-serif; font-weight: 700;
    color: var(--teal); font-size: 25px; letter-spacing: .5px; text-transform: uppercase;
  }
  .person-role {
    font-family: "Lato", sans-serif; color: var(--ink-grey); font-size: 19px; margin-top: 2px;
  }
  .divider { width: 180px; height: 1px; background: var(--rule); margin: 10px 0 8px; }
  .contact {
    font-family: "Lato", sans-serif; color: var(--ink-grey); font-size: 19px; line-height: 1.45;
  }
  .social {
    position: absolute; left: 0; right: 0; bottom: 24px;
    display: flex; align-items: center; justify-content: center; gap: 10px;
    font-family: "Lato", sans-serif; color: var(--paper); font-size: 20px;
  }
  .social-dot {
    width: 28px; height: 28px; border: 1.5px solid var(--paper); border-radius: 50%;
  }
</style>
</head>
<body>
  <main class="sheet">
    <section class="card card--back" aria-label="Card back">
      <div class="upper">
        <p class="brand-name--light">Harbourline<br>Electrical Solutions</p>
      </div>
      <ul class="services">
        <li>Electrical Construction &amp; Maintenance</li>
        <li>LED Lighting &amp; Automation</li>
        <li>Data &amp; Communication</li>
        <li>Life Safety Systems (Fire Alarm / Security)</li>
      </ul>
    </section>

    <section class="card card--front" aria-label="Card front">
      <div class="front-content">
        <div class="brand">
          <span class="brand-mark"></span>
          <span class="brand-name">Harbourline Electrical Solutions</span>
        </div>
        <p class="sectors">Commercial Industrial Residential</p>
        <h1 class="person-name">Marcus T. Hollings</h1>
        <p class="person-role">Project Manager</p>
        <div class="divider"></div>
        <p class="contact">(441) 555-0187</p>
        <p class="contact">hlelectricalsolutions@mailvento.com</p>
      </div>
      <div class="band"></div>
      <p class="social"><span class="social-dot"></span>@hlelectricalsolutions</p>
    </section>
  </main>
</body>
</html>
```